International Film making Business needs the 5 Logos provided made into a POSTER Format

Design Task:
CREATE A POSTER DESIGN USING THE 5 LOGOS PROVIDED. The BOLD BRIGHT HORIZON LOGO should stand out from the others by being in the middle with the other 4 logos connected to it somehow.

The 5 Businesses already has their 5 Logos, all similar in design to each other.

BOLD BRIGHT HORIZON is the Main Logo that encompasses the other 4 Logos. So it must stand out more and it is like the Overall Business entity that incorporates the other 4 Logos.

What is required is that by using the 5 Logo designs provided, create a cool graphic artwork that somehow incorporates ALL of the 5 Logos - But having the BOLD BRIGHT HORIZON Logo at the forefront/most important/standing out the most.
- BOLD BRIGHT HORIZON will probably be bigger than the others
- and could be changed into 3D.

I have attached all 5 logos and a hand drawn example of how the BOLD BRIGHT HORIZONS could stand out from the rest.

THE DESIGNS OF THE LOGOS SHOULD NOT BE CHANGED (except the BOLDBRIGHTHORIZON which can be 3D)

Please do not be restricted with the sample idea. Creativity is encouraged

DIMENSION: 3000 mm x 6000 mm
high resolution graphic

Logo Text

bold bright , bold bright pictures, bold bright legends, bold bright groovy, BOLD BRIGHT HORIZONS

Requirements
Must have
• USE THE 5 LOGOS PROVIDED ONLY - Only BOLD BRIGHT HORIZON can be changed into 3D only
Nice to have
• Eye catching design, showing the Bold Bright Horizon as the most powerful Logo that has the other 4 as subordinate companies
Should not have
• ANY CHANGE IN THE 5 LOGO DESIGNS (EXcept 3D for Bold Bright Onward)

```html
<!DOCTYPE html>
<html lang="en">
<head>
<meta charset="utf-8">
<title>Bold Bright Onward – Group Poster</title>
<link rel="stylesheet" href="https://fonts.googleapis.com/css2?family=Cinzel:wght@700&family=Montserrat:wght@500&display=swap">
<style>
  :root {
    --bg-deep: #6f7f92;
    --bg-mid: #b3bfcb;
    --bg-light: #eef2f6;
    --frame: #d9d6cc;
    --swoosh-dark: #7d8a99;
    --swoosh-light: #f4f6f9;
    --oval: #ffffff;
    --gold: #b8892f;
    --silver-ink: #5b5f66;
    --blue: #2a7fc4;
    --rainbow: #c2307a;
    --film: #2b2b2b;
    --groovy: #6a1f9c;
  }
  * { margin: 0; padding: 0; box-sizing: border-box; }
  html, body { width: 1200px; height: 600px; overflow: hidden; }
  body { font-family: "Cinzel", "Times New Roman", serif; }

  .poster {
    position: relative;
    width: 1200px;
    height: 600px;
    background:
      radial-gradient(ellipse 40% 42% at 47% 38%, var(--bg-light) 0%, rgba(238,242,246,0) 70%),
      linear-gradient(180deg, var(--bg-deep) 0%, var(--bg-mid) 40%, var(--bg-light) 56%, var(--bg-mid) 72%, var(--bg-deep) 100%);
    overflow: hidden;
  }
  .poster__art { position: absolute; inset: 0; }

  .brand {
    position: absolute;
    display: flex;
    align-items: center;
    justify-content: center;
    font-weight: 700;
    line-height: 1.05;
    letter-spacing: 0.04em;
    text-align: left;
  }
  .brand--sub { width: 326px; height: 160px; font-size: 27px; }
  .brand--blue   { left: 47px;  top: 45px;  color: var(--blue); }
  .brand--legend { left: 809px; top: 43px;  color: var(--rainbow); }
  .brand--film   { left: 49px;  top: 377px; color: var(--film); }
  .brand--groovy { left: 809px; top: 391px; color: var(--groovy); }

  .brand__mark {
    flex: none;
    border-radius: 50%;
    margin-right: 14px;
  }
  .brand--sub .brand__mark { width: 44px; height: 44px; background: currentColor; }

  .master {
    position: absolute;
    left: 335px;
    top: 192px;
    width: 480px;
    height: 180px;
    display: flex;
    align-items: center;
  }
  .master .brand__mark {
    width: 160px; height: 160px;
    background: var(--gold);
    margin-right: 16px;
  }
  .master__text { display: flex; flex-direction: column; }
  .master__name {
    color: var(--gold);
    font-weight: 700;
    font-size: 40px;
    line-height: 1.08;
    letter-spacing: 0.03em;
  }
  .master__url {
    font-family: "Montserrat", "Helvetica", sans-serif;
    font-weight: 500;
    font-size: 17px;
    color: var(--silver-ink);
    letter-spacing: 0.04em;
    margin-top: 4px;
    text-align: right;
  }
</style>
</head>
<body>
<main class="poster">
  <svg class="poster__art" width="1200" height="600" viewBox="0 0 1200 600" aria-hidden="true">
    <defs>
      <linearGradient id="swoosh" x1="0" y1="0" x2="1" y2="1">
        <stop offset="0" stop-color="var(--swoosh-light)"/>
        <stop offset="0.5" stop-color="var(--swoosh-dark)"/>
        <stop offset="1" stop-color="var(--swoosh-light)"/>
      </linearGradient>
      <filter id="lift" x="-20%" y="-20%" width="140%" height="140%">
        <feDropShadow dx="4" dy="8" stdDeviation="6" flood-color="#2c3440" flood-opacity="0.45"/>
      </filter>
    </defs>

    <rect class="frame" x="79" y="50" width="1037" height="511" fill="none" stroke="var(--frame)" stroke-width="1.5"/>

    <g class="swooshes" fill="none" stroke="url(#swoosh)" stroke-linecap="round">
      <ellipse cx="590" cy="300" rx="390" ry="185" stroke-width="22" transform="rotate(-8 590 300)"/>
      <ellipse cx="230" cy="150" rx="200" ry="95" stroke-width="14" transform="rotate(12 230 150)"/>
      <ellipse cx="990" cy="150" rx="200" ry="95" stroke-width="14" transform="rotate(-12 990 150)"/>
      <ellipse cx="230" cy="455" rx="200" ry="95" stroke-width="14" transform="rotate(-12 230 455)"/>
      <ellipse cx="990" cy="455" rx="200" ry="95" stroke-width="14" transform="rotate(12 990 455)"/>
    </g>

    <g class="badges" fill="var(--oval)" filter="url(#lift)">
      <ellipse cx="210" cy="125" rx="163" ry="80"/>
      <ellipse cx="972" cy="123" rx="163" ry="80"/>
      <ellipse cx="212" cy="457" rx="163" ry="80"/>
      <ellipse cx="972" cy="471" rx="163" ry="80"/>
    </g>
  </svg>

  <div class="brand brand--sub brand--blue"><span class="brand__mark"></span><span>BOLD<br>BRIGHT</span></div>
  <div class="brand brand--sub brand--legend"><span class="brand__mark"></span><span>BOLD BRIGHT<br>LEGENDS</span></div>
  <div class="brand brand--sub brand--film"><span class="brand__mark"></span><span>BOLD BRIGHT<br>PICTURES</span></div>
  <div class="brand brand--sub brand--groovy"><span class="brand__mark"></span><span>BOLD BRIGHT<br>GROOVY</span></div>

  <div class="master">
    <span class="brand__mark"></span>
    <div class="master__text">
      <span class="master__name">BOLD BRIGHT<br>ONWARD</span>
      <span class="master__url">boldbrightonward.example</span>
    </div>
  </div>
</main>
</body>
</html>
```